Telecommunications/Power civil contractor needs business card design

Were a new telecommunications/power underground civil contractor that is looking for a new business card design. Our company colours are silver or grey and orange. Feel free to use the white background logo or the black background logo.

Target Market(s)

Local contractors, utility companies, private sector mining/energy companies, developers.

Industry/Entity Type

Telecommunications

Contact Information for Business Card

Each card will need the following info:
Persons name:
Title:
E-mail:
Phone number:
Shop Address:
Mailing Address:

Requirements
Must have
• Each card will need the following info:
• Persons name:
• Title:
• E-mail:
• Phone number:
• Shop Address:
• Mailing Address:

```html
<!DOCTYPE html>
<html lang="en">
<head>
<meta charset="utf-8">
<title>Dig Line Contracting Inc – Business Card</title>
<link rel="stylesheet" href="https://fonts.googleapis.com/css2?family=Montserrat:wght@400;500;600;800&display=swap">
<style>
  :root {
    --orange: #ee6a2a;
    --grey: #7d7d7f;
    --grey-light: #a3a3a5;
    --ink: #2b2b2b;
    --card: #ffffff;
    --backdrop: #e9e7e3;
  }
  * { margin: 0; padding: 0; box-sizing: border-box; }
  html, body {
    width: 1200px;
    height: 1022px;
    overflow: hidden;
    background: var(--backdrop);
    font-family: "Montserrat", sans-serif;
  }
  .business-card {
    position: absolute;
    left: 100px;
    top: 225px;
    width: 1000px;
    height: 572px;
    background: var(--card);
    border-radius: 22px;
    overflow: hidden;
    box-shadow: 0 6px 24px rgba(0,0,0,0.12);
  }
  .edge-band {
    position: absolute;
    left: 0; top: 0; bottom: 0;
    width: 34px;
    background: var(--orange);
  }
  .brand-ring {
    position: absolute;
    left: 520px;
    top: 40px;
    width: 400px;
    height: 400px;
  }
  .details {
    position: absolute;
    left: 78px;
    top: 58px;
    color: var(--ink);
  }
  .company-name {
    font-weight: 800;
    font-size: 52px;
    line-height: 1;
    letter-spacing: 1px;
    color: var(--grey);
    text-transform: uppercase;
  }
  .company-suffix {
    font-weight: 800;
    font-size: 26px;
    line-height: 1.2;
    letter-spacing: 1px;
    color: var(--grey);
    text-transform: uppercase;
    margin-top: 4px;
  }
  .person-name {
    margin-top: 20px;
    font-weight: 500;
    font-size: 36px;
    letter-spacing: 1px;
    color: var(--orange);
    text-transform: uppercase;
  }
  .person-title {
    font-size: 22px;
    font-weight: 500;
    margin-top: 2px;
  }
  .address {
    margin-top: 22px;
    font-size: 22px;
    line-height: 1.4;
    font-weight: 400;
    letter-spacing: 0.5px;
  }
  .contact-list {
    list-style: none;
    margin-top: 20px;
    font-size: 22px;
    line-height: 1.4;
    letter-spacing: 0.5px;
  }
  .contact-list li {
    display: flex;
    align-items: center;
    gap: 14px;
  }
  .contact-icon {
    width: 20px;
    height: 20px;
    flex: none;
  }
</style>
</head>
<body>
  <main class="business-card">
    <div class="edge-band"></div>

    <svg class="brand-ring" viewBox="0 0 400 400" aria-hidden="true">
      <circle cx="200" cy="200" r="186" fill="none" stroke="#8a8a8c" stroke-width="16"/>
    </svg>

    <section class="details">
      <h1 class="company-name">Dig Line</h1>
      <p class="company-suffix">Contracting Inc</p>

      <h2 class="person-name">Marcus Ellery</h2>
      <p class="person-title">Director</p>

      <p class="address">
        48 Foundry Lane<br>
        Millbrook, NY 12345<br>
        PO BOX 3150<br>
        OAK HOLLOW, CA 90000
      </p>

      <ul class="contact-list">
        <li>
          <svg class="contact-icon" viewBox="0 0 20 20" aria-hidden="true">
            <rect x="3" y="3" width="14" height="14" rx="2" fill="none" stroke="#ee6a2a" stroke-width="2"/>
          </svg>
          +330 5550-0142
        </li>
        <li>
          <svg class="contact-icon" viewBox="0 0 20 20" aria-hidden="true">
            <path d="M5 2 L8 2 L9 6 L7 8 Q9 12 12 13 L14 11 L18 12 L18 15 Q17 18 14 18 Q4 16 2 5 Q2 2 5 2 Z" fill="#ee6a2a"/>
          </svg>
          +330 5550-0198
        </li>
        <li>
          <svg class="contact-icon" viewBox="0 0 20 20" aria-hidden="true">
            <rect x="2" y="4" width="16" height="12" fill="none" stroke="#ee6a2a" stroke-width="2"/>
            <path d="M2 4 L10 11 L18 4" fill="none" stroke="#ee6a2a" stroke-width="2"/>
          </svg>
          info@diglinecontracting.com
        </li>
        <li>
          <svg class="contact-icon" viewBox="0 0 20 20" aria-hidden="true">
            <circle cx="10" cy="10" r="8" fill="none" stroke="#ee6a2a" stroke-width="2"/>
            <ellipse cx="10" cy="10" rx="3.5" ry="8" fill="none" stroke="#ee6a2a" stroke-width="1.5"/>
            <path d="M2 10 H18 M4 6 H16 M4 14 H16" stroke="#ee6a2a" stroke-width="1.5"/>
          </svg>
          www.diglinecontracting.com
        </li>
      </ul>
    </section>
  </main>
</body>
</html>
```